Frostvale Harborline LLC

we need a business card design

Industry/Entity Type

hvac

Contact Information for Business Card

my logo

Requirements
Must have
• my logo and same colors

```html
<!DOCTYPE html>
<html lang="en">
<head>
<meta charset="utf-8">
<title>Frostvale Harborline LLC — Business Card</title>
<link rel="stylesheet" href="https://fonts.googleapis.com/css2?family=Montserrat:wght@400;500;700;800&display=swap">
<style>
  :root {
    --sun: #f6b851;
    --harbor-blue: #1658a5;
    --paper: #ffffff;
    --ink: #1d1d1f;
    --stage: #e9e6e1;
  }
  * { box-sizing: border-box; margin: 0; padding: 0; }
  html, body { width: 1200px; height: 931px; overflow: hidden; }
  body {
    background: var(--stage);
    font-family: "Montserrat", Arial, sans-serif;
    position: relative;
  }
  .card {
    position: absolute;
    width: 700px;
    height: 400px;
    border-radius: 22px;
    overflow: hidden;
    box-shadow: 0 10px 26px rgba(0,0,0,.18);
  }
  .card-front { left: 60px; top: 45px; background: var(--sun); }
  .card-back  { left: 440px; top: 486px; background: var(--paper); }

  .wordmark {
    display: flex;
    align-items: center;
    gap: 14px;
    color: var(--harbor-blue);
    font-weight: 800;
    line-height: 1.05;
  }
  .wordmark-dot {
    flex: none;
    border-radius: 50%;
    background: var(--harbor-blue);
  }
  .card-front .wordmark {
    position: absolute; left: 0; right: 0; top: 0; bottom: 0;
    justify-content: center;
    font-size: 40px;
  }
  .card-front .wordmark-dot { width: 40px; height: 40px; }

  .card-back .wordmark {
    position: absolute; right: 44px; top: 52px;
    font-size: 26px;
    text-align: left;
  }
  .card-back .wordmark-dot { width: 28px; height: 28px; }

  .rule {
    position: absolute; left: 40px; right: 40px; top: 196px;
    height: 2px; background: var(--harbor-blue);
  }
  .person { position: absolute; left: 40px; top: 132px; }
  .person-name { color: var(--harbor-blue); font-weight: 800; font-size: 32px; }
  .person-role { color: var(--ink); font-weight: 500; font-size: 17px; margin-top: 2px; }

  .contacts { position: absolute; left: 40px; top: 220px; list-style: none; }
  .contacts li {
    display: flex; align-items: center; gap: 12px;
    font-size: 17px; color: var(--ink); height: 30px;
  }
  .contacts svg { width: 18px; height: 18px; flex: none; }

  .address {
    position: absolute; right: 44px; top: 222px;
    font-size: 15px; color: var(--ink); text-align: right; line-height: 1.4;
  }
  .base-band {
    position: absolute; left: 0; right: 0; bottom: 0; height: 36px;
    background: var(--sun);
  }
</style>
</head>
<body>
  <section class="card card-front" aria-label="Card front">
    <div class="wordmark"><span class="wordmark-dot"></span><span>Frostvale Harborline LLC</span></div>
  </section>

  <section class="card card-back" aria-label="Card back">
    <div class="wordmark"><span class="wordmark-dot"></span><span>Frostvale<br>Harborline LLC</span></div>

    <div class="person">
      <p class="person-name">Dana Whitlow</p>
      <p class="person-role">Managing Director</p>
    </div>
    <div class="rule"></div>

    <ul class="contacts">
      <li>
        <svg viewBox="0 0 18 18" aria-hidden="true"><rect x="4" y="1" width="10" height="16" rx="2" fill="none" stroke="#f6b851" stroke-width="2"/></svg>
        +1 (555) 010-2468
      </li>
      <li>
        <svg viewBox="0 0 18 18" aria-hidden="true"><rect x="1" y="4" width="16" height="11" rx="1" fill="#f6b851"/><path d="M1 4l8 6 8-6" fill="none" stroke="#fff" stroke-width="1.4"/></svg>
        info@frostvaleharbor.com
      </li>
      <li>
        <svg viewBox="0 0 18 18" aria-hidden="true"><circle cx="9" cy="9" r="8" fill="#f6b851"/><path d="M1 9h16M9 1c-3 4-3 12 0 16M9 1c3 4 3 12 0 16" fill="none" stroke="#fff" stroke-width="1.2"/></svg>
        www.frostvaleharbor.com
      </li>
    </ul>

    <p class="address">48 Quay Road,<br>Harbor Falls, FL 33602</p>
    <div class="base-band"></div>
  </section>
</body>
</html>
```